high end kitchens , needing new logo and business card design .

im looking a very simple looking design but classy that will stand out , i would like the design to be in the colours black , silver , gold and grey , although all colours dont need to be used in design , back of card to have name on it derek fawcett , address and phone number and website address , maybe fb logo . adrress is 42 mill row , kilbrennan , bt19 4qa , 07912488265 , front of the card im open to design , back of card very simple i will want it matt black with silver writing , writing doesnt need to be that big

Target Market(s)

people with kitchen projects .

Industry/Entity Type

Interior Design

Contact Information for Business Card

front of business card th on it with maybe tallow hearths under it wrote smaller , maybe the card to be mate black with the writing in a gloss black or silver

Logo Text

th . tallow hearths

Font styles to use
Sans Serif
Script

Colors
1b1b1b
919191
f6f6f6
848484
ffc214
ec1f27

Requirements
Must have
• clean and simple , not too fussy ,
Nice to have
• n/a
Should not have
• n/a

```html
<!DOCTYPE html>
<html lang="en">
<head>
<meta charset="utf-8">
<title>Tallow Hearths — Business Card</title>
<link rel="stylesheet" href="https://fonts.googleapis.com/css2?family=Jost:wght@400;500&display=swap">
<style>
  :root {
    --backdrop: #0e0e0e;
    --card: #1b1b1b;
    --card-edge: #222222;
    --silver: #919191;
    --silver-soft: #848484;
    --divider: #3a3a3a;
  }
  * { margin: 0; padding: 0; box-sizing: border-box; }
  html, body {
    width: 1200px;
    height: 900px;
    overflow: hidden;
    background: var(--backdrop);
    font-family: "Jost", sans-serif;
  }
  .sheet {
    position: relative;
    width: 1200px;
    height: 900px;
  }
  .card {
    position: absolute;
    left: 280px;
    width: 640px;
    height: 366px;
    background: var(--card);
    border: 1px solid var(--card-edge);
    box-shadow: 0 18px 40px rgba(0,0,0,0.6);
  }
  .card--front { top: 60px; }
  .card--back { top: 470px; }

  .front-name {
    position: absolute;
    left: 0; right: 0;
    top: 150px;
    text-align: center;
    font-size: 46px;
    font-weight: 400;
    letter-spacing: 2px;
    color: var(--silver);
    text-transform: uppercase;
  }

  .brand {
    position: absolute;
    left: 40px;
    width: 260px;
    top: 130px;
    display: flex;
    flex-direction: column;
    align-items: center;
    gap: 16px;
  }
  .brand-dot {
    width: 40px; height: 40px;
    border-radius: 50%;
    background: var(--silver-soft);
  }
  .brand-name {
    font-size: 27px;
    font-weight: 400;
    letter-spacing: 1px;
    color: var(--silver);
    text-transform: uppercase;
    white-space: nowrap;
  }

  .divider {
    position: absolute;
    left: 322px;
    top: 80px;
    width: 1px;
    height: 200px;
    background: var(--divider);
  }

  .contact {
    position: absolute;
    left: 360px;
    top: 88px;
    color: var(--silver);
    font-size: 16px;
    line-height: 1.3;
    letter-spacing: 0.6px;
    white-space: nowrap;
  }
  .contact-name {
    font-size: 20px;
    letter-spacing: 2px;
    text-transform: uppercase;
    margin-bottom: 20px;
    color: var(--silver-soft);
  }
  .contact-address { margin-top: 14px; }
</style>
</head>
<body>
  <main class="sheet">
    <section class="card card--front" aria-label="Card front">
      <h1 class="front-name">Tallow Hearths</h1>
    </section>

    <section class="card card--back" aria-label="Card back">
      <div class="brand">
        <span class="brand-dot"></span>
        <span class="brand-name">Tallow Hearths</span>
      </div>
      <div class="divider"></div>
      <div class="contact">
        <p class="contact-name">Derek Fawcett</p>
        <p class="contact-phone">07912488265</p>
        <p class="contact-email">info@tallowhearths.com</p>
        <p class="contact-web">www.tallowhearths.com</p>
        <p class="contact-address">42 mill row ,<br>kilbrennan , bt19 4qa</p>
      </div>
    </section>
  </main>
</body>
</html>
```